Redesign of business card for Cedar Ridge Mechanical

We are looking for a new design for our business cards for Cedar Ridge Mechanical. We are a plumbing & HVAC construction company, operating on the West Coast of Canada and USA. Logo attached.
Industry/Entity Type
Construction - Plumbing & HVAC
Contact Information for Business Card
Name, address, phone numbers, email, website address
Look and feel
Each slider illustrates characteristics of the customer's brand and the style your logo design should communicate.

```html
<!DOCTYPE html>
<html lang="en">
<head>
<meta charset="utf-8">
<title>Cedar Ridge Mechanical – Business Card</title>
<link href="https://fonts.googleapis.com/css2?family=Montserrat:wght@400;500;700;800&display=swap" rel="stylesheet">
<style>
  :root{
    --stage:#2a2a2a;
    --card:#141414;
    --card-soft:#1c1c1c;
    --white:#ffffff;
    --grey:#8c8c8c;
    --ink:#1a1a1a;
  }
  *{margin:0;padding:0;box-sizing:border-box}
  html,body{width:1200px;height:963px;overflow:hidden;background:var(--stage);font-family:'Montserrat',sans-serif}
  .card{position:absolute;left:260px;width:680px;height:388px;border-radius:18px;overflow:hidden;box-shadow:0 14px 40px rgba(0,0,0,.45)}
  .card--front{top:60px}
  .card--back{top:515px;background:radial-gradient(ellipse at 50% 45%,var(--card-soft),var(--card) 75%)}
  .card svg.bg{position:absolute;inset:0}
  .brand{position:absolute;display:flex;align-items:center;gap:14px;color:var(--white);font-weight:800;letter-spacing:.06em;text-transform:uppercase}
  .brand__mark{background:var(--white);display:block}
  .card--front .brand{top:92px;left:0;right:0;justify-content:center;font-size:26px}
  .card--front .brand__mark{width:26px;height:26px}
  .card--back .brand{top:0;bottom:0;left:0;right:0;justify-content:center;font-size:34px}
  .card--back .brand__mark{width:34px;height:34px}
  .person{position:absolute;left:52px;top:252px;text-align:right;width:230px}
  .person__name{font-weight:800;font-size:22px;color:var(--ink);letter-spacing:.02em;white-space:nowrap}
  .person__name span{color:var(--grey)}
  .person__role{font-size:15px;color:var(--grey);margin-top:2px}
  .divider{position:absolute;left:302px;top:250px;width:1px;height:64px;background:var(--grey)}
  .contacts{position:absolute;left:320px;top:246px;list-style:none;font-size:17px;color:var(--ink);line-height:24px}
  .contacts li{display:flex;align-items:center;gap:8px;white-space:nowrap}
  .contacts svg{width:15px;height:15px;flex:none}
  .contacts b{font-weight:700}
  .address{position:absolute;left:40px;top:340px;font-size:16px;color:var(--grey);white-space:nowrap}
</style>
</head>
<body>
  <section class="card card--front">
    <svg class="bg" viewBox="0 0 680 388" width="680" height="388" aria-hidden="true">
      <rect width="680" height="388" fill="var(--card)"/>
      <rect x="0" y="212" width="680" height="10" fill="var(--grey)"/>
      <rect x="170" y="212" width="400" height="10" fill="var(--white)"/>
      <path d="M0,230 H680 V388 H480 C430,388 420,322 370,322 H0 Z" fill="var(--white)"/>
    </svg>
    <div class="brand"><i class="brand__mark"></i>Cedar Ridge Mechanical</div>
    <div class="person">
      <p class="person__name">DANIEL <span>REEVES</span></p>
      <p class="person__role">Manager</p>
    </div>
    <div class="divider"></div>
    <ul class="contacts">
      <li><svg viewBox="0 0 16 16"><path d="M3 1h3l1.5 4-2 1.2a9 9 0 0 0 4.3 4.3L11 8.5l4 1.5v3a2 2 0 0 1-2 2A13 13 0 0 1 1 3a2 2 0 0 1 2-2z" fill="var(--ink)"/></svg><span>604-555-0187</span></li>
      <li><svg viewBox="0 0 16 16"><rect x="1" y="3" width="14" height="10" rx="1" fill="var(--ink)"/><path d="M1.5 4 8 9l6.5-5" stroke="var(--white)" stroke-width="1.4" fill="none"/></svg><span>youremail@cedarridge.com</span></li>
      <li><svg viewBox="0 0 16 16"><circle cx="8" cy="8" r="7" fill="var(--ink)"/><path d="M1 8h14M8 1c-3 3-3 11 0 14M8 1c3 3 3 11 0 14" stroke="var(--white)" stroke-width="1" fill="none"/></svg><span>www.<b>yourwebsite</b>.com</span></li>
    </ul>
    <p class="address">Your address, city, state, ZIP 0000</p>
  </section>

  <section class="card card--back">
    <div class="brand"><i class="brand__mark"></i>Cedar Ridge Mechanical</div>
  </section>
</body>
</html>
```